Push notification screens at app start up

We have an existing news publication app platform and are adding categories to push notifications.

We need two screens designed (each for Zorbel, Quillet and Android for a total of 6d) that show when the app is first launched.

The workflow of our app:
0. app launch screen while webservices run (no work needed)
1. information screen to the user promoting the benefits of push notification with "Next" button. (see concept attached)
2. Push categories selection screen. This will have list of category types, with on/off switch.

"Select the categories that you wish to receive occasional notices:
Breaking News (on/off switch)
Local News (on/off switch)
Sports (on/off switch)
Local Events (on/off switch)
Weather Alerts (on/off switch)
Local Deals (on/off switch)"

"Enable these categories on the next screen."
"Next" button

Background:
When I was looking around at app designs, I came across this one (http://www.plinthworks.example/design/7719034) and I really liked it. We obviously have different features on our screen, but I’d like to have this same feel. The colors used in this design are perfect.

UPDATE: I do not mean to limit your design to match the layout as the one mentioned above. Please use your creativity for the layout.

Our standard font in Helvetica Neue.

Notes:
- our app is developed for all phone devices from Zorbel 4 to Zorbel 6, so designs should be thoughtful of vertical scrolling if needed.
- our app is developed for Quillets, so we'll need designs completed as well. (We can finalize Zorbel design first, then translate the design to Quillet.)
- our app is developed for Android phones (not tablets), so we'll need designs completed as well. (We can finalize iOS design first, then translater to Android UI design guidelines).

We hope to establish a good on-going relationship with the designer for as-needed work in the future.

News

• Helvetica Neue

• Clean designs. No clutter.
• We would likely go with the standard on/off switches for both iOS and Android, but are open to small custom variations.

```html
<!DOCTYPE html>
<html lang="en">
<head>
<meta charset="utf-8">
<title>Notifications – Onboarding</title>
<link href="https://fonts.googleapis.com/css2?family=Arimo:wght@400;700&display=swap" rel="stylesheet">
<style>
  :root {
    --header-bg: #4f4f4f;
    --header-stripe: #585858;
    --ring: #6a6a6a;
    --accent: #2570f4;
    --page-bg: #e7e7e7;
    --card-bg: #ffffff;
    --text-dark: #2b2b2b;
    --divider: #d9d9d9;
    --white: #ffffff;
  }
  * { box-sizing: border-box; margin: 0; padding: 0; }
  html, body { width: 675px; height: 1200px; overflow: hidden; }
  body {
    font-family: "Arimo", "Helvetica Neue", Arial, sans-serif;
    background: var(--page-bg);
    position: relative;
    color: var(--text-dark);
  }
  .header {
    position: absolute; left: 0; top: 0; width: 675px; height: 367px;
    background: repeating-linear-gradient(135deg, var(--header-bg) 0 6px, var(--header-stripe) 6px 8px);
  }
  .header-pointer {
    position: absolute; left: 318px; top: 366px; width: 0; height: 0;
    border-left: 19px solid transparent; border-right: 19px solid transparent;
    border-top: 18px solid var(--header-bg);
  }
  .status-bar {
    position: absolute; left: 0; top: 0; width: 675px; height: 40px;
    color: var(--white); font-size: 22px;
    display: flex; align-items: center; justify-content: space-between; padding: 0 12px;
  }
  .status-left, .status-right { display: flex; align-items: center; gap: 8px; }
  .status-time { position: absolute; left: 0; right: 0; text-align: center; font-weight: 700; pointer-events: none; }
  .badge {
    position: absolute; left: 247px; top: 95px; width: 180px; height: 180px;
    border-radius: 50%; border: 6px solid var(--ring);
    display: flex; align-items: center; justify-content: center;
  }
  .badge-core {
    width: 150px; height: 150px; border-radius: 50%; background: var(--accent);
    display: flex; align-items: center; justify-content: center;
  }
  .card {
    position: absolute; left: 27px; top: 432px; width: 621px; height: 524px;
    background: var(--card-bg); border-radius: 16px; text-align: center;
  }
  .card-title {
    font-size: 44px; font-weight: 700; padding-top: 38px; height: 108px;
    border-bottom: 2px solid var(--divider); margin: 0 0;
  }
  .card-body { font-size: 20px; line-height: 30px; padding: 36px 20px 0; }
  .card-body p + p { margin-top: 30px; }
  .btn-next {
    position: absolute; left: 18px; top: 403px; width: 585px; height: 96px;
    background: var(--accent); color: var(--white); border: none; border-radius: 8px;
    font-family: inherit; font-size: 32px; font-weight: 700; letter-spacing: 1px;
  }
</style>
</head>
<body>
  <div class="header"></div>
  <div class="header-pointer"></div>

  <div class="status-bar">
    <div class="status-left">
      <svg width="58" height="12" viewBox="0 0 58 12" aria-hidden="true">
        <g fill="#fff"><circle cx="5" cy="6" r="5"/><circle cx="17" cy="6" r="5"/><circle cx="29" cy="6" r="5"/></g>
        <g fill="none" stroke="#fff" stroke-width="1.2"><circle cx="41" cy="6" r="4.4"/><circle cx="53" cy="6" r="4.4"/></g>
      </svg>
      <span>KESTREL</span>
      <svg width="24" height="18" viewBox="0 0 24 18" aria-hidden="true">
        <path d="M12 17 L3 7 A13 13 0 0 1 21 7 Z" fill="#fff"/>
      </svg>
    </div>
    <div class="status-time">4:21 PM</div>
    <div class="status-right">
      <svg width="12" height="20" viewBox="0 0 12 20" aria-hidden="true">
        <path d="M1 5 L11 14 L6 19 V1 L11 6 L1 15" fill="none" stroke="#fff" stroke-width="1.6"/>
      </svg>
      <span>100%</span>
      <svg width="46" height="20" viewBox="0 0 46 20" aria-hidden="true">
        <rect x="1" y="1" width="40" height="18" rx="3" fill="none" stroke="#fff" stroke-width="1.6"/>
        <rect x="4" y="4" width="34" height="12" rx="1.5" fill="#fff"/>
        <rect x="42" y="7" width="3" height="6" rx="1" fill="#fff"/>
      </svg>
    </div>
  </div>

  <div class="badge">
    <div class="badge-core">
      <svg width="84" height="70" viewBox="0 0 84 70" aria-hidden="true">
        <g fill="none" stroke="#fff" stroke-width="4" stroke-linejoin="round" stroke-linecap="round">
          <path d="M6 28 L16 24 L52 8 L52 58 L16 42 L6 40 Z"/>
          <path d="M16 24 V42"/>
          <path d="M20 44 L26 62 H34 L30 48"/>
          <path d="M60 24 A12 12 0 0 1 60 42"/>
          <path d="M68 16 A22 22 0 0 1 68 50"/>
        </g>
      </svg>
    </div>
  </div>

  <main class="card">
    <h1 class="card-title">Notifications</h1>
    <div class="card-body">
      <p>By enabling push notifications, you can keep up to<br>date with occasional notifications related to items you<br>care about. Select the categories on the next screen<br>and then authorize the push notifications.</p>
      <p>If you ever change your mind, you can adjust these<br>options in the Settings menu of this app.</p>
    </div>
    <button class="btn-next" type="button">NEXT</button>
  </main>
</body>
</html>
```